Business cards for Harbourline Supply Pty Ltd that import building products into Australia from China
Target Market(s)
Business to Business
Industry/Entity Type
Business
Contact Information for Business Card
Front: Logo and Business Name
Rear:
Desmond Varrick
General Manager
Mobile: 0427 561 394
email: dessie@harbourlinesupply.com.au
alternative email: dessie@outbackworks.com.au
web: www.harbourlinesupply.com.au
Calder, Marlow Bay and Tindall
Colors
ec1f27
fbee3d

```html
<!DOCTYPE html>
<html lang="en">
<head>
<meta charset="utf-8">
<title>Harbourline Supply Pty Ltd – Business Cards</title>
<link rel="stylesheet" href="https://fonts.googleapis.com/css2?family=Exo+2:wght@400;500;700;800&display=swap">
<style>
  :root {
    --bg: #b6b6b6;
    --red: #ec1f27;
    --yellow: #fbee3d;
    --ink: #1c1c1c;
    --white: #ffffff;
    --rule: #d9b8bb;
  }
  * { margin: 0; padding: 0; box-sizing: border-box; }
  html, body { width: 1200px; height: 900px; overflow: hidden; }
  body {
    background: var(--bg);
    font-family: "Exo 2", sans-serif;
    position: relative;
  }
  .card {
    position: absolute;
    top: 184px;
    height: 491px;
    border-radius: 14px;
    overflow: hidden;
  }
  .card--details { left: 299px; width: 301px; background: var(--white); }
  .card--brand { left: 645px; width: 305px; background: var(--red); }

  .tab {
    position: absolute;
    left: 80px;
    width: 141px;
    height: 12px;
    background: var(--red);
  }
  .tab--top { top: 0; }
  .tab--bottom { bottom: 0; }

  .brand-name {
    position: absolute;
    left: 0; right: 0;
    text-align: center;
    font-weight: 800;
    line-height: 1.05;
  }
  .brand-name .mark {
    display: block;
    width: 40px; height: 40px;
    margin: 0 auto 14px;
  }
  .brand-name .word { display: block; font-size: 28px; letter-spacing: -0.3px; }
  .brand-name .legal { display: block; font-size: 14px; letter-spacing: 1.5px; margin-top: 6px; }

  .card--details .brand-name { top: 70px; color: var(--ink); }
  .card--details .mark { background: var(--red); }
  .card--brand .brand-name { top: 186px; color: var(--white); }
  .card--brand .mark { background: var(--yellow); }

  .person { position: absolute; left: 32px; top: 256px; }
  .person__name { font-size: 21px; font-weight: 700; letter-spacing: 0.6px; color: var(--ink); }
  .person__name .first { color: var(--red); }
  .person__role { font-size: 14px; font-weight: 500; color: var(--ink); margin-top: 1px; }

  .contacts { position: absolute; left: 32px; top: 312px; list-style: none; }
  .contacts li {
    display: flex; align-items: center;
    height: 22px;
    font-size: 13.5px;
    color: var(--ink);
  }
  .contacts svg { width: 12px; height: 12px; margin: 0 10px 0 1px; flex: none; fill: var(--red); }

  .rule {
    position: absolute; left: 32px; width: 236px; top: 411px;
    height: 1px; background: var(--rule);
  }
  .locations {
    position: absolute; left: 0; right: 0; top: 424px;
    text-align: center;
    font-size: 14px; color: var(--ink);
  }
</style>
</head>
<body>
  <section class="card card--details" aria-label="Business card, contact side">
    <div class="tab tab--top"></div>
    <div class="brand-name">
      <span class="mark"></span>
      <span class="word">Harbourline Supply</span>
      <span class="legal">PTY LTD</span>
    </div>
    <div class="person">
      <p class="person__name"><span class="first">DESMOND</span> VARRICK</p>
      <p class="person__role">General Manager</p>
    </div>
    <ul class="contacts">
      <li><svg viewBox="0 0 24 24" aria-hidden="true"><path d="M6.6 10.8a15.2 15.2 0 0 0 6.6 6.6l2.2-2.2c.3-.3.7-.4 1-.2 1.1.4 2.3.6 3.6.6.6 0 1 .4 1 1V20c0 .6-.4 1-1 1A17 17 0 0 1 3 4c0-.6.4-1 1-1h3.5c.6 0 1 .4 1 1 0 1.3.2 2.5.6 3.6.1.3 0 .7-.2 1z"/></svg>0427 561 394</li>
      <li><svg viewBox="0 0 24 24" aria-hidden="true"><path d="M2 5h20v14H2z"/><path d="M4 7l8 6 8-6" fill="none" stroke="#fff" stroke-width="1.6"/></svg>dessie@harbourlinesupply.com.au</li>
      <li><svg viewBox="0 0 24 24" aria-hidden="true"><path d="M2 5h20v14H2z"/><path d="M4 7l8 6 8-6" fill="none" stroke="#fff" stroke-width="1.6"/></svg>dessie@outbackworks.com.au</li>
      <li><svg viewBox="0 0 24 24" aria-hidden="true"><circle cx="12" cy="12" r="10"/><path d="M2 12h20M12 2c3 3 3 17 0 20M12 2c-3 3-3 17 0 20" fill="none" stroke="#fff" stroke-width="1.4"/></svg>www.harbourlinesupply.com.au</li>
    </ul>
    <div class="rule"></div>
    <p class="locations">Calder, Marlow Bay and Tindall</p>
    <div class="tab tab--bottom"></div>
  </section>

  <section class="card card--brand" aria-label="Business card, brand side">
    <div class="brand-name">
      <span class="mark"></span>
      <span class="word">Harbourline Supply</span>
      <span class="legal">PTY LTD</span>
    </div>
  </section>
</body>
</html>
```